VL - menu design

Hi,

We require elegant menu design for upscale restaurant. Please find attached the logo and the menu items for your reference.

for inspiration, this is a good website: -
http://www.plateworthy-sample.net/dishcraft/about.php

We are very much open for Menu Size suggestions.

unfortunately the place is going under renovation, we don't have updated images to it. the closest look and feel to our place is http://vazelo-example.com ..

we are also open for creative options on the shape, the styles, etc. as long as it represents the fine dine feel ...

Thanks ...

Dear All,

We wouldlike to extend our apology for not being able to provide feedbacks on everysingle design. We were extremely busy and we have multiple contests opensimultaneously which makes the process even harder.

However,we would like to thank you all for the efforts you have put into designingour menu. It is very much appreciated …

We wishyou all success in your design ventures and we are quite positive that we willbe working with many of you on many projects in the soon future. 

Thanks & Regards,

DQI Team...

 

 

 

Industry/Entity Type

Restaurant

Requirements
Must have
• Please ensure that there are 'some' images in the menu ... this is very important.
Should not have
• IMPORTANT: -

1. Please DO NOT insert any currency sign to the menu
2. Please keep the prices of the menu at the end of the menu items descriptions NOT beside the menu item names. The font of the price should be similar to the menu item description and please DO NOT bold the numbers. the prices should be subtle.

Thank you ...

```html
<!DOCTYPE html>
<html lang="en">
<head>
<meta charset="utf-8">
<title>The Sandwiches – Menu</title>
<link href="https://fonts.googleapis.com/css2?family=Ubuntu:wght@300;400;500&display=swap" rel="stylesheet">
<style>
  :root {
    --panel-brown: #8a7152;
    --badge-cream: #f1ede8;
    --text-cream: #f4ece0;
    --heading-brown: #8a7152;
    --dash-cream: #efe7dc;
    --photo-bread: #d9b98a;
    --photo-green: #7fa845;
    --photo-red: #b8332b;
    --photo-plum: #7a3d5c;
  }
  html, body {
    margin: 0;
    padding: 0;
    width: 1200px;
    height: 2700px;
    overflow: hidden;
    background: var(--panel-brown);
  }
  .menu-panel {
    position: relative;
    width: 1200px;
    height: 2700px;
    background: var(--panel-brown);
    font-family: "Ubuntu", Arial, sans-serif;
    overflow: hidden;
  }
  .dash-line {
    position: absolute;
    width: 0;
    border-left: 3px dashed var(--dash-cream);
  }
  .dash-line--top { left: 285px; top: 0; height: 82px; }
  .dash-line--large-photo { left: 785px; top: 2500px; height: 200px; }
  .dash-line--small-photo { left: 271px; top: 2596px; height: 104px; }

  .section-badge {
    position: absolute;
    left: 70px;
    top: 80px;
    width: 432px;
    height: 432px;
    border-radius: 50%;
    background: var(--badge-cream);
    display: flex;
    flex-direction: column;
    align-items: center;
    justify-content: center;
    color: var(--heading-brown);
    text-transform: uppercase;
    line-height: 1;
  }
  .section-badge__pre {
    font-weight: 300;
    font-size: 50px;
    margin-top: -14px;
  }
  .section-badge__title {
    margin: 4px 0 0;
    font-weight: 500;
    font-size: 61px;
  }

  .dish-list {
    position: absolute;
    left: 94px;
    top: 582px;
    width: 1090px;
    margin: 0;
    padding: 0;
    list-style: none;
    color: var(--text-cream);
    font-weight: 300;
    font-size: 48px;
    letter-spacing: 1px;
    line-height: 60px;
    white-space: nowrap;
  }
  .dish { margin: 0 0 60px; }
  .dish--tight { margin-bottom: 0; }
  .dish__price { font-weight: 300; }

  .dish-photo {
    position: absolute;
    border-radius: 50%;
    border: 4px solid #ffffff;
    box-sizing: border-box;
  }
  .dish-photo--large {
    left: 456px;
    top: 1824px;
    width: 676px;
    height: 680px;
    background:
      linear-gradient(180deg,
        var(--photo-bread) 0%, #c99e62 16%,
        var(--photo-plum) 24%, var(--photo-green) 34%,
        #e9d9b0 44%, var(--photo-bread) 55%,
        var(--photo-red) 66%, var(--photo-green) 74%,
        #e9d9b0 82%, var(--photo-bread) 100%);
  }
  .dish-photo--small {
    left: 80px;
    top: 2220px;
    width: 384px;
    height: 380px;
    background:
      linear-gradient(180deg,
        #e9d9b0 0%, var(--photo-plum) 14%,
        var(--photo-green) 30%, var(--photo-bread) 42%,
        var(--photo-red) 56%, #e9d9b0 68%,
        var(--photo-bread) 82%, #f6f4f0 100%);
  }
</style>
</head>
<body>
<main class="menu-panel">
  <span class="dash-line dash-line--top"></span>

  <header class="section-badge">
    <span class="section-badge__pre">The</span>
    <h1 class="section-badge__title">Sandwiches</h1>
  </header>

  <ul class="dish-list">
    <li class="dish">Grilled Vegetables Sandwich with fresh Goat<br>cheese and chives served with our<br>Homemade spicy garlic mayo. <span class="dish__price">59</span></li>
    <li class="dish">Butterfish burger with fresh tomato, beef<br>bacon, grilled vegetables and béarnaise<br>sauce.</li>
    <li class="dish">Tataki Tuna sandwich with red onion slices,<br>stewed endives and black olives and sulta-<br>nas pate’. <span class="dish__price">79</span></li>
    <li class="dish dish--tight">Beef sirloin steak sandwich with grain mus-<br>tard, Parmesan cheese and fresh<br>Nashi pears. <span class="dish__price">79</span></li>
    <li class="dish">The Traditional Club sandwich served with<br>French fries and vegetable chips. <span class="dish__price">69</span></li>
    <li class="dish">Chicken sandwich with Parmesan cheese<br>slices, sundried tomatoes and mint<br>Flavored mayo. <span class="dish__price">69</span></li>
  </ul>

  <div class="dish-photo dish-photo--large" role="img" aria-label="Photo of a grilled vegetable sandwich on toasted bread with peppers, zucchini, red onion and goat cheese"></div>
  <div class="dish-photo dish-photo--small" role="img" aria-label="Photo of a halved grilled vegetable sandwich with red pepper and herbed cheese"></div>

  <span class="dash-line dash-line--large-photo"></span>
  <span class="dash-line dash-line--small-photo"></span>
</main>
</body>
</html>
```